Business card

We need a business card design for our company based in Auckland , New Zealand called 'Ridge + Studio Ltd'. We provide architectural services. We would like to see designs that use the max. three colours (such as white, black, grey) The final design should communicate financial safety and growth."
Also I will provide our company logo. I would like to the logo to be embeded onto our business card.

Target Market(s)

new residential house, alteration & addition & light commericila design & drafting service

Industry/Entity Type

Architecture

Contact Information for Business Card

Company name: ridge + studio Ltd.
Name: Mark Delford
Job title: architectural designer & Design LBP
email address: mark@rplusd.co.nz
mobile number: 02 5163 2290
web site: www.rplusd.co.nz

Requirements
Must have
• My project must have..
• - embeded logo (attached company logo)
• I don't have a bigger version for our company logo, but I have one old one, so you can remove the word from it)
• - insert the attached small BKTW logo & LBP logo
• - creative, simple and clear business card.
• - Max. three colours
Nice to have
• - Here are the samples I would like to share with you: http://www.plimvora.com/blog/minimalistic-business-card-designs/
• I would like to have my business card like one of the creation.
Should not have
• TBA

```html
<!DOCTYPE html>
<html lang="en">
<head>
<meta charset="utf-8">
<title>Ridge + Studio Ltd — Business Card</title>
<link rel="stylesheet" href="https://fonts.googleapis.com/css2?family=Open+Sans:wght@400;600;700&display=swap">
<style>
  :root {
    --backdrop: #e4e4e4;
    --card: #ffffff;
    --ink: #111111;
    --mist: #d9d9d9;
    --stone: #8a8a8a;
  }
  * { margin: 0; padding: 0; box-sizing: border-box; }
  html, body { width: 1200px; height: 849px; overflow: hidden; }
  body {
    background: var(--backdrop);
    font-family: "Open Sans", Arial, sans-serif;
    color: var(--ink);
    position: relative;
  }
  .card {
    position: absolute;
    top: 332px;
    width: 345px;
    height: 222px;
    background: var(--card);
  }
  .card--front {
    left: 204px;
    border: 14px solid var(--ink);
    display: flex;
    align-items: center;
    justify-content: center;
  }
  .wordmark {
    font-weight: 700;
    letter-spacing: -0.01em;
    white-space: nowrap;
  }
  .card--front .wordmark { font-size: 24px; }
  .card--back { left: 617px; }
  .card--back .wordmark {
    position: absolute;
    top: 38px;
    left: 0;
    width: 100%;
    text-align: center;
    font-size: 11px;
    padding-left: 26px;
  }
  .company-name {
    position: absolute;
    top: 88px;
    left: 0;
    width: 100%;
    text-align: center;
    font-size: 15px;
    font-weight: 700;
    padding-left: 26px;
  }
  .job-title {
    position: absolute;
    top: 110px;
    left: 0;
    width: 100%;
    text-align: center;
    font-size: 6px;
    font-weight: 600;
    padding-left: 40px;
  }
  .contact {
    position: absolute;
    top: 140px;
    left: 40px;
    display: grid;
    grid-template-columns: 117px auto;
    column-gap: 7px;
    row-gap: 0;
    font-size: 8.5px;
    line-height: 11.5px;
  }
  .contact dt { text-align: right; }
  .contact dd { font-weight: 400; }
  .badge {
    position: absolute;
    left: 303px;
    top: 182px;
    width: 27px;
    height: 27px;
    border-radius: 50%;
    background: var(--ink);
    border: 3px solid var(--card);
    box-shadow: 0 0 0 1px var(--stone);
  }
</style>
</head>
<body>
  <section class="card card--front" aria-label="Business card front">
    <span class="wordmark">ridge + studio</span>
  </section>

  <section class="card card--back" aria-label="Business card back">
    <span class="wordmark">ridge + studio</span>
    <h1 class="company-name">ridge + studio Ltd.</h1>
    <p class="job-title">architectural designer &amp; Design LBP</p>
    <dl class="contact">
      <dt>Name:</dt><dd>Mark Delford</dd>
      <dt>email address:</dt><dd>mark@rplusd.co.nz</dd>
      <dt>mobile number:</dt><dd>02 5163 2290</dd>
      <dt>web site:</dt><dd>www.rplusd.co.nz</dd>
    </dl>
    <span class="badge" role="img" aria-label="BKTW membership badge"></span>
  </section>
</body>
</html>
```